Verdant Systems Business Card

want the back of card to be blue- with the logo in the center
front of card- info plus logo (info being mailing address, email address, and website address )
4 different names with titles to have on cards
1) Calvin Borsted - Owner
2) Naomi Trelvik- Customer Relationship Specialist
3) Felix Andrade- Vice President of Sales
4) Owen Markby- Chief Technology Officer

Target Market(s)

tech company in the government/probation office industry

Industry/Entity Type

Government Office

Contact Information for Business Card

1) Calvin Borsted - Owner

Colors
0355a3
ffffff

Requirements
Must have
• back side should be blue, with the logo placed in the center
• front side needs to include both the logo, as well as company info (info should include website address, email address, and mailing address)

```html
<!DOCTYPE html>
<html lang="en">
<head>
<meta charset="utf-8">
<title>Verdant Systems Business Card</title>
<link href="https://fonts.googleapis.com/css2?family=Cinzel:wght@700&family=Lato:wght@400&display=swap" rel="stylesheet">
<style>
  :root {
    --backdrop: #2a2a2b;
    --navy: #1a2d55;
    --white: #ffffff;
    --band-grey: #808083;
    --text-grey: #6d6e72;
  }
  * { margin: 0; padding: 0; box-sizing: border-box; }
  html, body { width: 1200px; height: 802px; overflow: hidden; }
  body { background: var(--backdrop); position: relative; font-family: "Lato", sans-serif; }

  .card {
    position: absolute;
    top: 274px;
    width: 443px;
    height: 264px;
    overflow: hidden;
    box-shadow: 0 3px 8px rgba(0,0,0,.55);
  }
  .card--front { left: 136px; background: var(--white); }
  .card--back { left: 624px; background: var(--navy); }

  .brand {
    position: absolute;
    left: 0; right: 0;
    display: flex;
    align-items: center;
    justify-content: center;
    gap: 10px;
  }
  .brand__mark { width: 22px; height: 22px; }
  .brand__name {
    font-family: "Cinzel", serif;
    font-weight: 700;
    font-size: 27px;
    letter-spacing: 0.5px;
    white-space: nowrap;
  }
  .card--front .brand { top: 34px; }
  .card--front .brand__name { color: var(--navy); }
  .card--front .brand__mark { background: var(--navy); }
  .card--back .brand { top: 99px; }
  .card--back .brand__name { color: var(--white); }
  .card--back .brand__mark { background: var(--white); }

  .mailing-address {
    position: absolute;
    left: 0; right: 0;
    top: 80px;
    text-align: center;
    color: var(--text-grey);
    font-size: 12.5px;
    white-space: nowrap;
  }

  .team-band {
    position: absolute;
    left: 0; top: 124px;
    width: 100%; height: 96px;
    background: var(--navy);
  }
  .member { position: absolute; color: var(--white); }
  .member__name {
    font-family: "Cinzel", serif;
    font-weight: 700;
    font-size: 16.5px;
    line-height: 18px;
    white-space: nowrap;
  }
  .member__title { font-size: 13px; line-height: 15px; white-space: nowrap; }
  .member--a { left: 33px; top: 11px; }
  .member--b { left: 217px; top: 11px; }
  .member--c { left: 33px; top: 52px; }
  .member--d { left: 217px; top: 52px; }

  .contact-band {
    position: absolute;
    left: 0; top: 227px;
    width: 100%; height: 37px;
    background: var(--band-grey);
    color: var(--white);
    font-size: 12.5px;
    display: flex;
    align-items: center;
    justify-content: center;
    white-space: nowrap;
  }
  .contact-band .sep { margin: 0 8px; }

  .address-band {
    position: absolute;
    left: 0; top: 208px;
    width: 100%; height: 31px;
    background: var(--band-grey);
    color: var(--white);
    font-size: 12.5px;
    display: flex;
    align-items: center;
    justify-content: center;
  }
</style>
</head>
<body>
  <section class="card card--front" aria-label="Card front">
    <div class="brand">
      <span class="brand__mark"></span>
      <span class="brand__name">Verdant Systems</span>
    </div>
    <div class="mailing-address">421, Address line here, 45452,Country Name</div>
    <div class="team-band">
      <div class="member member--a">
        <div class="member__name">CALVIN BORSTED</div>
        <div class="member__title">Owner</div>
      </div>
      <div class="member member--b">
        <div class="member__name">NAOMI TRELVIK</div>
        <div class="member__title">Customer Relationship Specialist</div>
      </div>
      <div class="member member--c">
        <div class="member__name">FELIX ANDRADE</div>
        <div class="member__title">Vice President of Sales</div>
      </div>
      <div class="member member--d">
        <div class="member__name">OWEN MARKBY</div>
        <div class="member__title">Chief Technology Officer</div>
      </div>
    </div>
    <div class="contact-band">
      <span>support@VerdantSystems.com</span><span class="sep">|</span><span>www.VerdantSystems.com</span>
    </div>
  </section>

  <section class="card card--back" aria-label="Card back">
    <div class="brand">
      <span class="brand__mark"></span>
      <span class="brand__name">Verdant Systems</span>
    </div>
    <div class="address-band">421, Address line here, 45452,Country Name</div>
  </section>
</body>
</html>
```